Medical Billing Company Needs a Business Card Design

We need a business card design for a Florida based medical billing company called 'Clinicians Keystone Solutions'. We specialize in providing revenue cycle management services to physician and therapist offices (we're basically their back-office processing partner for providing billing software, claims submissions, A/R follow-up and patient statements & collections. Our logo is red and blue-ish, so make sure that whatever other elements are used will match appropriately. Our current business card design has a too small font size. I'd like to project an image that shows we are modern & reliable. On a side note, I'm planning on using ZUB for printing these cards.

Target Market(s)

Office managers, physicians, therapists

Industry/Entity Type

Printing

Requirements
Must have
• Logo
Name of Employee
Phone
Fax
E-mail
Website

```html
<!DOCTYPE html>
<html lang="en">
<head>
<meta charset="utf-8">
<title>Clinicians Keystone Solutions – Business Card</title>
<link href="https://fonts.googleapis.com/css2?family=Open+Sans:wght@400;600;700&display=swap" rel="stylesheet">
<style>
  :root {
    --navy: #2a1f7a;
    --purple-light: #5b4a9e;
    --purple-dark: #1f0f6b;
    --red: #a8121c;
    --ink: #3c3c44;
    --rule: #c8c8d0;
    --paper: #ffffff;
    --backdrop: #e4e4ea;
  }
  html, body {
    margin: 0;
    width: 1200px;
    height: 987px;
    overflow: hidden;
    background: var(--backdrop);
    font-family: "Open Sans", Arial, sans-serif;
  }
  .sheet {
    width: 1200px;
    height: 987px;
    display: flex;
    flex-direction: column;
    align-items: center;
    justify-content: center;
    gap: 40px;
  }
  .card {
    position: relative;
    width: 760px;
    height: 434px;
    background: var(--paper);
    border-radius: 26px;
    overflow: hidden;
    box-shadow: 0 6px 18px rgba(40, 40, 70, 0.18);
  }
  .card__art {
    position: absolute;
    inset: 0;
  }
  .brand {
    position: absolute;
    display: flex;
    align-items: center;
    gap: 12px;
    color: var(--navy);
    font-weight: 600;
    letter-spacing: 1px;
    white-space: nowrap;
  }
  .brand__mark {
    width: 14px;
    height: 14px;
    background: var(--red);
  }
  .front .brand { left: 42px; top: 168px; font-size: 30px; }
  .contacts {
    position: absolute;
    left: 42px;
    top: 240px;
    margin: 0;
    padding: 0;
    list-style: none;
    color: var(--ink);
    font-size: 17px;
    line-height: 28px;
  }
  .contacts li { display: flex; align-items: center; gap: 10px; }
  .contacts svg { width: 15px; height: 15px; fill: var(--navy); }
  .divider {
    position: absolute;
    left: 42px;
    top: 362px;
    width: 300px;
    height: 1px;
    background: var(--rule);
  }
  .address {
    position: absolute;
    left: 42px;
    top: 372px;
    color: var(--ink);
    font-size: 17px;
    line-height: 24px;
  }
  .person {
    position: absolute;
    right: 30px;
    top: 290px;
    text-align: right;
    color: #fff;
  }
  .person__name { font-size: 28px; font-weight: 700; line-height: 1.15; }
  .person__title { font-size: 20px; }
  .back .brand {
    left: 0; right: 0; top: 168px;
    justify-content: center;
    font-size: 44px;
  }
  .back .web {
    position: absolute;
    left: 0; right: 0; top: 246px;
    text-align: center;
    color: var(--ink);
    font-size: 19px;
    letter-spacing: 4px;
  }
</style>
</head>
<body>
<main class="sheet">

  <section class="card front" aria-label="Card front">
    <svg class="card__art" viewBox="0 0 760 434" aria-hidden="true">
      <defs>
        <linearGradient id="band-purple" x1="0" y1="0" x2="1" y2="1">
          <stop offset="0" stop-color="#5b4a9e"/>
          <stop offset="1" stop-color="#1f0f6b"/>
        </linearGradient>
      </defs>
      <path class="band" d="M0 0 H760 V434 H580 C540 140 380 30 0 30 Z" fill="url(#band-purple)"/>
      <path class="stripe-thin" d="M0 37 C375 37 532 146 572 434" fill="none" stroke="var(--red)" stroke-width="3"/>
      <path class="stripe-wide" d="M0 50 C365 52 518 154 554 434" fill="none" stroke="var(--red)" stroke-width="10"/>
    </svg>

    <div class="brand"><span class="brand__name">CLINICIANS KEYSTONE</span><span class="brand__mark"></span></div>

    <ul class="contacts">
      <li><svg viewBox="0 0 16 16"><path d="M3 1h3l1 4-2 1a9 9 0 0 0 5 5l1-2 4 1v3c0 1-1 2-2 2A13 13 0 0 1 1 3c0-1 1-2 2-2z"/></svg>123-456-0789</li>
      <li><svg viewBox="0 0 16 16"><path d="M4 0h8a1 1 0 0 1 1 1v14a1 1 0 0 1-1 1H4a1 1 0 0 1-1-1V1a1 1 0 0 1 1-1zm1 2v9h6V2zm3 10.5a1 1 0 1 0 0 2 1 1 0 0 0 0-2z"/></svg>123-456-0789</li>
      <li><svg viewBox="0 0 16 16"><path d="M1 3h14v10H1zm1 1.5V12h12V4.5L8 9z"/></svg>info@clinicianskeystone.com</li>
      <li><svg viewBox="0 0 16 16"><path d="M8 0a8 8 0 1 0 0 16A8 8 0 0 0 8 0zm0 1.5c1 0 2 2 2.3 5.5H5.7C6 3.5 7 1.5 8 1.5zM1.6 9h2.6c.1 2 .5 3.6 1.1 4.8A6.5 6.5 0 0 1 1.6 9zm0-2a6.5 6.5 0 0 1 3.7-4.8C4.7 3.4 4.3 5 4.2 7zm4.1 2h4.6C10 12.5 9 14.5 8 14.5S6 12.5 5.7 9zm5 4.8c.6-1.2 1-2.8 1.1-4.8h2.6a6.5 6.5 0 0 1-3.7 4.8zM11.8 7c-.1-2-.5-3.6-1.1-4.8A6.5 6.5 0 0 1 14.4 7z"/></svg>www.clinicianskeystone.com</li>
    </ul>

    <div class="divider"></div>
    <div class="address">Street Name, City Name<br>State Zip Code</div>

    <div class="person">
      <div class="person__name">Your Name</div>
      <div class="person__title">Title</div>
    </div>
  </section>

  <section class="card back" aria-label="Card back">
    <div class="brand"><span class="brand__name">CLINICIANS KEYSTONE</span><span class="brand__mark"></span></div>
    <div class="web">www.clinicianskeystone.com</div>
  </section>

</main>
</body>
</html>
```